Brochure for a civil enineering company in A4 format

I need a brochure design for our company TIRO Engineering S.r.l.. We are an engineering consultant company. Our main clients are from the infrastructure industry (geotechnical and underground sectors mainly).
We are looking for a 2 pages (4 faces) fold out design with a glued pocket where we can put individual data sheets.
I need A4 format pages.

Target Market(s)

We are an engineering consultant company. Our main clients are from the infrastructure industry (geotechnical and underground sectors mainly).

Industry/Entity Type

Civil Engineer

Font styles to use
Sans Serif

Requirements
Must have
• Overall: 2 pages in A4 format
Essential style. Bright and modern appearance.
Glued pocket
Logo integrated in a picture on the pocket where I would like to insert a slogan (… tiro engineering … reliable solutions …)
Attached are selected images which the designer can use and edit at their own discretion.
Some advice in the following (anyway designers are free to provide their solutions):
Outer sheets:
Front page with name, logo. It could be nice to have the “m” of the logo integrated in a pictures, also a modified picture (I mean modify one of the attached pictures) so to create a general image and do not tie the cover to a specific job.
Back page: offices address and contact email address. Nice to have one space for a slogan.
Inner sheet: text that I upload in the file “inside-sheets”, possibly with pictures on each sheet. In the right faces insert the glued pocket. On this pages insert the section OUR EXPERIENCE ….with a space for a picture of our team.
Nice to have
• Clean and essential design.
Pictures choosing from the atteched ones. Pictures could be modified in a very light manner to make them a general idea of the work ( I mean geotechnical world) without to be immediately linked to a specific site.
Should not have
• excessive frills

```html
<!DOCTYPE html>
<html lang="en">
<head>
<meta charset="utf-8">
<title>TIRO Engineering S.r.l. – Brochure</title>
<link rel="stylesheet" href="https://fonts.googleapis.com/css2?family=Montserrat:wght@300;400;600;700&family=Open+Sans:wght@400;600&display=swap">
<style>
  :root{
    --bg:#e6e6e8;
    --paper:#ffffff;
    --ink:#262626;
    --ink-soft:#5d5d5f;
    --ink-faint:#9a9a9c;
    --band:#1f1f20;
    --rule:#d4d4d6;
    --sky:#5f93c9;
    --crane:#b8413a;
    --steel:#8d9095;
    --tunnel-dark:#2c3440;
    --tunnel-light:#7e8c9e;
  }
  *{box-sizing:border-box;margin:0;padding:0}
  html,body{width:889px;height:1200px;overflow:hidden}
  body{background:var(--bg);font-family:"Open Sans",Arial,sans-serif;color:var(--ink);position:relative}

  .spread{position:absolute;left:44px;width:800px;height:566px;display:flex;box-shadow:0 6px 18px rgba(0,0,0,.18)}
  .spread--outer{top:36px}
  .spread--inner{top:612px}
  .page{position:relative;width:400px;height:566px;background:var(--paper);overflow:hidden}
  .page--left{border-right:1px solid var(--rule)}

  .heading{font-family:"Montserrat",Arial,sans-serif;font-size:12px;letter-spacing:.06em;text-transform:uppercase;color:var(--ink)}
  .heading b{font-weight:700}
  .heading span{font-weight:300}
  .body-text{font-size:7.5px;line-height:1.75;color:var(--ink-soft);text-align:justify}
  .wordmark{font-family:"Montserrat",Arial,sans-serif;font-weight:600;color:var(--ink);letter-spacing:.02em}

  /* back page */
  .back-texture{position:absolute;inset:0;background:linear-gradient(150deg,#f4f4f5 0%,#ffffff 45%,#efeff0 100%)}
  .offices{position:absolute;left:34px;top:228px;width:170px}
  .offices .heading{margin-bottom:14px}
  .office{margin-bottom:12px}
  .office-label{font-family:"Montserrat",Arial,sans-serif;font-size:7px;font-weight:600;color:var(--ink);margin-bottom:4px}
  .contact-line{display:flex;align-items:center;gap:6px;font-size:6.5px;color:var(--ink-soft);margin-bottom:3px}
  .contact-line svg{width:8px;height:8px;flex:none}
  .back-mark{position:absolute;left:0;right:0;bottom:40px;text-align:center;font-size:18px}

  /* front page */
  .front-mark{position:absolute;left:0;right:0;top:34px;text-align:center;font-size:28px}
  .photo{position:absolute}
  .photo--crane{left:70px;top:150px;width:185px;height:148px;background:linear-gradient(180deg,var(--sky) 0%,#9cc0e2 45%,var(--crane) 46%,#8f2f2a 70%,var(--steel) 100%)}
  .photo--tunnel{left:259px;top:150px;width:141px;height:148px;background:radial-gradient(ellipse at 50% 45%,var(--tunnel-light) 0%,#4b5868 45%,var(--tunnel-dark) 100%)}
  .front-title{position:absolute;right:0;top:304px;width:270px;text-align:right}
  .front-title .line-one{font-family:"Montserrat",Arial,sans-serif;font-weight:700;font-size:12px;letter-spacing:.04em;padding:4px 16px 4px 0;color:var(--ink)}
  .front-title .line-two{background:var(--band);color:#fff;font-family:"Montserrat",Arial,sans-serif;font-weight:400;font-size:11px;letter-spacing:.06em;padding:6px 16px 6px 0}
  .front-web{position:absolute;right:24px;bottom:30px;display:flex;align-items:center;gap:8px;font-size:6.5px;color:var(--ink-faint)}
  .front-web i{display:block;width:110px;height:1px;background:var(--rule)}

  /* inner left */
  .photo--band{left:0;top:0;width:400px;height:110px;background:linear-gradient(100deg,#151515 0%,#3a3d42 55%,#6c7178 100%)}
  .company-head{position:absolute;left:30px;top:78px}
  .company-head.heading{color:#fff}
  .company-text{position:absolute;left:30px;top:126px;width:340px}
  .services{position:absolute;left:30px;top:206px;width:340px}
  .services .heading{margin-bottom:10px}
  .services .body-text{margin-bottom:8px}

  /* inner right */
  .expertise{position:absolute;left:30px;top:40px;width:340px}
  .expertise .heading{margin-bottom:10px}
  .sub-bar{background:var(--band);color:#fff;font-family:"Montserrat",Arial,sans-serif;font-size:7px;font-weight:600;letter-spacing:.05em;text-transform:uppercase;padding:5px 10px;margin:4px 0 10px;width:220px}
  .expertise .body-text{margin-bottom:8px}
  .photo--site{left:30px;top:392px;width:168px;height:140px;background:linear-gradient(160deg,#a5adb7 0%,#6f6a60 60%,#4b4741 100%)}
  .photo--works{left:202px;top:392px;width:168px;height:140px;background:linear-gradient(200deg,#c5c9cc 0%,#8b8f7e 55%,#5b5f52 100%)}
</style>
</head>
<body>

<section class="spread spread--outer">
  <article class="page page--left back-page">
    <div class="back-texture" role="img" aria-label="Faint grey geometric texture"></div>
    <div class="offices">
      <h2 class="heading"><span>OUR</span> <b>OFFICES</b></h2>
      <div class="office">
        <p class="office-label">Head office</p>
        <p class="contact-line"><svg viewBox="0 0 10 10"><path d="M5 0.5a3.2 3.2 0 0 0-3.2 3.2C1.8 6 5 9.5 5 9.5S8.2 6 8.2 3.7A3.2 3.2 0 0 0 5 .5zm0 4.4a1.2 1.2 0 1 1 0-2.4 1.2 1.2 0 0 1 0 2.4z" fill="#5d5d5f"/></svg>Via Roma 12, 20121 Milano</p>
        <p class="contact-line"><svg viewBox="0 0 10 10"><path d="M2.2 0.8l1.6 0 .8 2.2-1.1.8a5.5 5.5 0 0 0 2.5 2.5l.8-1.1 2.2.8v1.6c0 .7-.6 1.2-1.3 1.1A7.9 7.9 0 0 1 1.1 2.1C1 1.4 1.5.8 2.2.8z" fill="#5d5d5f"/></svg>+39 02 0000 0000</p>
        <p class="contact-line"><svg viewBox="0 0 10 10"><rect x="0.8" y="2" width="8.4" height="6" fill="none" stroke="#5d5d5f" stroke-width="1"/><path d="M1 2.3l4 3 4-3" fill="none" stroke="#5d5d5f" stroke-width="1"/></svg>info@tiroengineering.example</p>
      </div>
      <div class="office">
        <p class="office-label">Branch office</p>
        <p class="contact-line"><svg viewBox="0 0 10 10"><path d="M5 0.5a3.2 3.2 0 0 0-3.2 3.2C1.8 6 5 9.5 5 9.5S8.2 6 8.2 3.7A3.2 3.2 0 0 0 5 .5zm0 4.4a1.2 1.2 0 1 1 0-2.4 1.2 1.2 0 0 1 0 2.4z" fill="#5d5d5f"/></svg>Corso Italia 8, 10121 Torino</p>
        <p class="contact-line"><svg viewBox="0 0 10 10"><path d="M2.2 0.8l1.6 0 .8 2.2-1.1.8a5.5 5.5 0 0 0 2.5 2.5l.8-1.1 2.2.8v1.6c0 .7-.6 1.2-1.3 1.1A7.9 7.9 0 0 1 1.1 2.1C1 1.4 1.5.8 2.2.8z" fill="#5d5d5f"/></svg>+39 011 0000 0000</p>
      </div>
    </div>
    <p class="wordmark back-mark">tiro</p>
  </article>

  <article class="page front-page">
    <p class="wordmark front-mark">tiro</p>
    <div class="photo photo--crane" role="img" aria-label="Red crawler crane lifting a tunnel boring machine section under blue sky"></div>
    <div class="photo photo--tunnel" role="img" aria-label="Interior of a lit underground tunnel"></div>
    <div class="front-title">
      <p class="line-one">LOREM IPSUM DOLOR SIT AMET</p>
      <p class="line-two">CONSECTETUR ADIPISCING</p>
    </div>
    <p class="front-web"><i></i>www.tiroengineering.example</p>
  </article>
</section>

<section class="spread spread--inner">
  <article class="page page--left company-page">
    <div class="photo photo--band" role="img" aria-label="Dark construction site banner photo"></div>
    <h2 class="heading company-head"><span>OUR</span> <b>COMPANY</b></h2>
    <p class="body-text company-text">We are an independent engineering consultancy serving the infrastructure sector. Our team designs geotechnical and underground works, from feasibility studies to construction support, with reliable solutions for every site.</p>
    <div class="services">
      <h2 class="heading"><span>OUR</span> <b>SERVICES</b></h2>
      <p class="body-text">Tunnel design, deep excavations, foundations, slope stability, monitoring plans and site supervision. We follow each project with care, combining field experience with advanced numerical analysis.</p>
      <p class="body-text">Our engineers work closely with contractors and owners to deliver safe, efficient and durable structures.</p>
      <p class="body-text">Geotechnical investigations are planned and interpreted in house, so that ground models, parameters and design choices remain consistent from the first survey to the final as built documents.</p>
      <p class="body-text">For underground works we provide excavation and support design, lining analysis, settlement prediction and interaction studies with existing buildings and services along the alignment.</p>
      <p class="body-text">During construction our staff on site checks monitoring data, updates the design where needed and supports the contractor in every critical phase of the work.</p>
      <p class="body-text">We also support public authorities with independent design reviews, technical audits and expert opinions on complex infrastructure projects.</p>
      <p class="body-text">Quality, safety and clear communication guide each phase, from tender to handover.</p>
    </div>
  </article>

  <article class="page experience-page">
    <div class="expertise">
      <h2 class="heading"><span>OUR</span> <b>EXPERTISE AND EXPERIENCE</b></h2>
      <p class="sub-bar">Twenty years in underground works</p>
      <p class="body-text">Our experience covers road and rail tunnels, metro lines, shafts and hydraulic works across Europe. Each assignment builds knowledge we bring to the next project, always with a practical approach.</p>
      <p class="body-text">Design reviews, risk assessment and construction monitoring are part of a single, coherent service.</p>
      <p class="body-text">Over the years we have worked on mechanised and conventional tunnelling in soft ground and rock, facing squeezing conditions, water inflows and difficult portals with tailored solutions.</p>
      <p class="body-text">Our geotechnical team has designed retaining walls, anchored diaphragms, pile foundations and slope stabilisation works for motorways, railways and urban developments.</p>
      <p class="sub-bar">Our team</p>
      <p class="body-text">Behind every project there is a group of engineers, geologists and technicians who share method, curiosity and a strong sense of responsibility towards clients and communities.</p>
      <p class="body-text">We invest in training and software so that every design is accurate, verified and ready for construction. Continuous dialogue with universities and research centres keeps our methods up to date with the latest codes and practice.</p>
    </div>
    <div class="photo photo--site" role="img" aria-label="Tunnel portal construction site"></div>
    <div class="photo photo--works" role="img" aria-label="Excavation works with machinery"></div>
  </article>
</section>

</body>
</html>
```